Redo a PPT pres. - Real Estate in Brazil - Socially equitable investments in Social Housing

We need to redo the presentation attached. It is an institutional presentation to attract local and foreign investors to invest in Brazilian Social Housing Projects structured by our company "TLR".
A middle class of 100 million, a housing deficit of 9M, a strong political will & positive income generation trends constitute grounds for a significant demand in social housing.
This make a perfect scheme for investors to invest in Brazilian Social Housing.
"TLR", is a consulting "boutique" focused in Brazilian real estate, specialized in structuring, analyzing and originating Brazilian social housing projects.
TLR is part of the group TLB. TLB is structured to create value through each step of the residential real estate business - structuring, financing, sales, marketing and technology.
We would like to see designs that use mainly the color blue. The final design should communicate financial safety and professionalism. In order to reach our needs, the designer will need to have basic understanding of finance and investment in order to highlight the most important information.
The idea is to receive back the PPT with each page redesigned and an homogeneous identity.
To all designers,
Target Market(s)
Institutional Investors and wealthy individuals
Industry/Entity Type
Residential
Look and feel

```html
<!DOCTYPE html>
<html lang="en">
<head>
<meta charset="utf-8">
<title>Social Housing in Brazil – TLR</title>
<link rel="stylesheet" href="https://fonts.googleapis.com/css2?family=Montserrat:wght@500;700&display=swap">
<style>
  :root {
    --sky-top: #5f86ad;
    --sky-mid: #3f6690;
    --city-low: #1d3656;
    --banner: #1c2433;
    --banner-alpha: rgba(24, 30, 44, 0.86);
    --white: #ffffff;
    --accent-green: #8cc63f;
    --logo-ink: #24366b;
  }
  * { box-sizing: border-box; margin: 0; padding: 0; }
  html, body {
    width: 1200px;
    height: 675px;
    overflow: hidden;
    background: var(--city-low);
  }
  .cover-slide {
    position: relative;
    width: 1200px;
    height: 675px;
    overflow: hidden;
    font-family: "Montserrat", Arial, sans-serif;
  }
  .skyline-photo {
    position: absolute;
    inset: 0;
    background:
      linear-gradient(180deg, rgba(255,255,255,0.08) 0%, rgba(0,0,0,0) 40%),
      linear-gradient(180deg, var(--sky-top) 0%, var(--sky-mid) 45%, var(--city-low) 100%);
  }
  .title-banner {
    position: absolute;
    left: 333px;
    top: 0;
    width: 534px;
    height: 622px;
  }
  .banner-content {
    position: absolute;
    left: 333px;
    top: 0;
    width: 534px;
    text-align: center;
    color: var(--white);
  }
  .deck-title {
    margin-top: 128px;
    font-weight: 700;
    font-size: 39px;
    line-height: 1.3;
    letter-spacing: 1.5px;
  }
  .deck-tagline {
    margin-top: 52px;
    font-weight: 500;
    font-size: 19px;
    line-height: 1.3;
    letter-spacing: 1px;
    color: var(--accent-green);
  }
  .brand-tile {
    display: inline-flex;
    align-items: center;
    gap: 7px;
    margin-top: 62px;
    width: 110px;
    height: 48px;
    justify-content: center;
    background: var(--white);
  }
  .brand-mark {
    width: 10px;
    height: 26px;
    background: var(--logo-ink);
  }
  .brand-name {
    font-weight: 700;
    font-size: 26px;
    color: var(--logo-ink);
  }
  .slide-footer {
    position: absolute;
    right: 40px;
    bottom: 20px;
    font-size: 11px;
    font-weight: 500;
    color: var(--accent-green);
  }
</style>
</head>
<body>
  <section class="cover-slide">
    <div class="skyline-photo" role="img" aria-label="Aerial photo of a dense high-rise city skyline by the water under a blue sky"></div>

    <svg class="title-banner" viewBox="0 0 534 622" aria-hidden="true">
      <polygon points="0,0 534,0 534,622 267,503 0,622" fill="var(--banner-alpha)"/>
    </svg>

    <div class="banner-content">
      <h1 class="deck-title">SOCIAL HOUSING<br>IN BRAZIL</h1>
      <p class="deck-tagline">HIGH YIELD RETURN FOR<br>A QUASI SOVEREIGN RISK</p>
      <div class="brand-tile">
        <span class="brand-mark"></span>
        <span class="brand-name">TLR</span>
      </div>
    </div>

    <p class="slide-footer">Investor Deck</p>
  </section>
</body>
</html>
```